Equipment Finance Specialist I work with companies who need the funds to buy their equipment

I would like a business card that stands out on the shelves. I want to be able to hand it to someone and say WOW. This card should have my logo.
You can put color into it I am very open on design and color

What my company does is we deal with dealerships that sell equipment such as Dump Trucks garbage trucks tractors trailers. Customers get referred to us and depending on their time in business we will ask for the following items

Companies that have been in business for more than two years we have a credit application program up to 250K . With this program we need the following items Credit application filled out(which is what I would like to be able for the customer to click on my website to get.) as well as three current month bank statements.

Deals over 250k we will need the following items

2 years business tax returns
2 years personal tax returns
Profit & Loss statement
Personal Financial Statement

what we do
100% FINANCING
SEASONAL PAYMENTS
LOAN BALLOON PAYMENTS
TRAC LEASING
LOW-INTEREST REFINANCING RATES
DEBT CONSOLIDATION

We specialize in creative financing solutions and offer a variety of reliable, flexible and expandable lending choices.

Target Market(s)

Trucking Companies

Industry/Entity Type

Trucking Company

Contact Information for Business Card

* $250,000 Application only Program
* Loans from $30,000 to 5,000,000
* Competitive Interest Rates

Font styles to use
Serif
Sans Serif

Colors

Designer to choose colors to be used in the design.

Requirements
Must have
• On the back of the card.
• * $250,000 Application only Program
• * Loans from $30,000 to 5,000,000
• My name, email, website. address
• * Competitive Interest Rates
• * 100% Financing
Nice to have
• I want my logo to pop on the card
• My logo is the great one I would like to use
Should not have
• I am up for your creativity as well

```html
<!DOCTYPE html>
<html lang="en">
<head>
<meta charset="utf-8">
<title>Summit Lending – Business Card</title>
<link rel="stylesheet" href="https://fonts.googleapis.com/css2?family=Roboto:wght@400;500;700&family=Open+Sans:wght@400&display=swap">
<style>
  :root {
    --navy: #10306e;
    --navy-deep: #0b2a66;
    --red: #c8102e;
    --grey: #6b6b6b;
    --silver-light: #eef0f3;
    --silver-dark: #a9aeb6;
    --white: #ffffff;
    --stage: #e9eaec;
  }
  * { margin: 0; padding: 0; box-sizing: border-box; }
  html, body { width: 1125px; height: 1200px; overflow: hidden; background: var(--stage); }
  .canvas { position: relative; width: 1125px; height: 1200px; }

  .card { position: absolute; left: 150px; width: 826px; height: 471px; overflow: hidden; }
  .card-front { top: 98px; background: var(--white); }
  .card-back { top: 631px; background: var(--navy-deep); }

  /* Front: brand */
  .brand { position: absolute; left: 57px; top: 178px; display: flex; align-items: center; gap: 16px; }
  .brand-dot { width: 112px; height: 112px; border-radius: 50%; background: var(--navy); }
  .brand-name { font-family: "Roboto", sans-serif; font-weight: 700; font-size: 40px; line-height: 1.05; color: var(--navy); letter-spacing: 1px; }

  .divider { position: absolute; left: 462px; top: 137px; width: 2px; height: 209px; background: #d9d9d9; }

  /* Front: contact */
  .contact { position: absolute; left: 498px; top: 133px; font-family: "Roboto", sans-serif; }
  .person-name { font-size: 28px; font-weight: 700; color: var(--navy); letter-spacing: 0.5px; }
  .person-title { font-size: 20px; font-weight: 700; color: var(--red); margin-top: 4px; letter-spacing: 0.5px; }
  .address { margin-top: 22px; font-size: 19px; font-weight: 500; color: var(--grey); line-height: 26px; letter-spacing: 0.3px; }
  .contact-row { display: flex; align-items: center; gap: 14px; color: var(--grey); font-weight: 500; }
  .contact-row svg { flex: none; }
  .phone { margin-top: 14px; font-size: 20px; letter-spacing: 0.5px; }
  .email { margin-top: 6px; font-size: 18px; }

  .footer-band { position: absolute; left: 0; bottom: 0; width: 826px; height: 48px; }
  .website { position: absolute; right: 20px; bottom: 11px; font-family: "Roboto", sans-serif; font-size: 19px; color: var(--white); letter-spacing: 1.6px; }

  /* Back */
  .emblem { position: absolute; left: 296px; top: 116px; width: 240px; height: 240px; border-radius: 50%;
            background: radial-gradient(circle at 35% 30%, var(--silver-light), var(--silver-dark));
            display: flex; align-items: center; justify-content: center; }
  .emblem-name { font-family: "Roboto", sans-serif; font-weight: 700; font-size: 34px; line-height: 1.1; color: var(--navy-deep); text-align: center; letter-spacing: 1px; }
  .offers { position: absolute; left: 0; top: 394px; width: 100%; text-align: center; font-family: "Open Sans", sans-serif; font-size: 20px; line-height: 26px; color: var(--white); }
</style>
</head>
<body>
<main class="canvas">
  <section class="card card-front">
    <div class="brand">
      <span class="brand-dot"></span>
      <span class="brand-name">SUMMIT<br>LENDING</span>
    </div>
    <div class="divider"></div>
    <div class="contact">
      <p class="person-name">MARK HALDEN</p>
      <p class="person-title">PRESIDENT</p>
      <p class="address">2170 Harbor Ridge Road<br>Lakeview, NY 11552</p>
      <p class="contact-row phone">
        <svg width="20" height="18" viewBox="0 0 20 18" aria-hidden="true"><path d="M2 5c0-3 16-3 16 0v2h-4V5H6v2H2z" fill="var(--navy)"/><rect x="4" y="8" width="12" height="9" rx="2" fill="var(--navy)"/><circle cx="10" cy="12.5" r="2.3" fill="var(--white)"/></svg>
        555 0142 7788
      </p>
      <p class="contact-row email">
        <svg width="20" height="14" viewBox="0 0 20 14" aria-hidden="true"><rect width="20" height="14" rx="1.5" fill="var(--navy)"/><path d="M1 1l9 7 9-7" stroke="var(--white)" stroke-width="1.6" fill="none"/></svg>
        mark@summitlending.com
      </p>
    </div>
    <svg class="footer-band" viewBox="0 0 826 48" aria-hidden="true">
      <rect x="0" y="32" width="490" height="16" fill="var(--red)"/>
      <polygon points="521,0 826,0 826,48 475,48" fill="var(--navy)"/>
    </svg>
    <p class="website">www.summitlending.com</p>
  </section>

  <section class="card card-back">
    <div class="emblem"><span class="emblem-name">SUMMIT<br>LENDING</span></div>
    <p class="offers">$250,000 Application only Program ● Loans from $30,000 to 5,000,000<br>Competitive Interest Rates ● 100% Financing</p>
  </section>
</main>
</body>
</html>
```